Website for new dental office

I am Dr. Colin Ashford and am building a new dental practice. I specialize in general dentistry. I am young and have a higher end dental practice incorporating very new technologies and would like my website to reflect that. As many dental patients are older, the website must be very easy to navigate. I would like patients to be able to request appointments, and will eventually add on patient information forms (the health history, etc, that you normally fill out in the practice) from my practice management software, so leave an area for that.

Industry/Entity Type

Building

```html
<!DOCTYPE html>
<html lang="en">
<head>
<meta charset="utf-8">
<title>Ashford Dental</title>
<link rel="stylesheet" href="https://fonts.googleapis.com/css2?family=Oswald:wght@500&family=Open+Sans:wght@600;700&family=Arimo:ital,wght@0,400;0,700;1,400;1,700&display=swap">
<style>
:root{
  --navy:#0c2456;
  --green:#9fd000;
  --text:#3d3d3d;
  --ink:#222;
  --welcome-bg:#f7f7f7;
  --lower-bg:#ebebeb;
  --footer-bg:#333333;
  --rule:#d6d6d6;
  --date:#1f3d7a;
}
*{margin:0;padding:0;box-sizing:border-box}
html,body{width:1041px;height:1200px;overflow:hidden}
body{position:relative;font-family:"Arimo",Arial,sans-serif;color:var(--text);background:#fff}
.hero{position:absolute;left:0;top:0;width:1041px;height:557px;
  background:linear-gradient(90deg,#9dbcdc 0%,#c3d8ec 30%,#e4ecf4 55%,#ece8f1 75%,#dcd3e4 100%)}
.header-curve{position:absolute;left:0;top:0}
.brand{position:absolute;left:95px;top:26px;display:flex;align-items:center;gap:12px}
.brand-mark{width:42px;height:42px;border-radius:50%;background:var(--navy)}
.brand-name{font-family:"Open Sans",sans-serif;font-weight:700;font-size:23px;line-height:28px;color:var(--navy);letter-spacing:.5px}
.contact{position:absolute;left:612px;top:20px;display:flex;align-items:center;gap:6px}
.contact small{font-size:11px;color:var(--ink)}
.contact strong{font-family:"Open Sans",sans-serif;font-weight:600;font-size:17px;color:var(--ink)}
.social{position:absolute;left:795px;top:15px;display:flex;gap:5px}
.social span{width:31px;height:31px;border-radius:50%;background:#1a55a8}
.patient-actions{position:absolute;right:87px;top:498px;display:flex;gap:10px}
.patient-actions a{display:block;height:36px;line-height:36px;padding:0 18px;border-radius:5px;font-family:"Open Sans",sans-serif;font-weight:700;font-size:13px;text-decoration:none}
.action-appointment{background:var(--green);color:#fff}
.action-forms{background:#fff;color:var(--navy);border:2px solid var(--navy);line-height:32px!important}
.nav{position:absolute;left:0;top:557px;width:1041px;height:55px;background:var(--navy)}
.nav a{position:absolute;top:12px;height:30px;line-height:30px;color:#fff;font-size:15px;text-decoration:none}
.nav a.active{background:var(--green);border-radius:5px;width:91px;text-align:center;color:#233}
.nav i{position:absolute;top:14px;width:1px;height:26px;background:#3a5186}
.welcome{position:absolute;left:0;top:612px;width:1041px;height:243px;background:var(--welcome-bg)}
h2{font-family:"Oswald",sans-serif;font-weight:500;font-size:26px;color:var(--navy);letter-spacing:.3px;transform:scaleX(.82);transform-origin:left}
h2 em{font-style:normal;color:var(--green)}
.welcome h2{position:absolute;left:95px;top:22px}
.welcome hr{position:absolute;left:95px;top:71px;width:859px;border:0;border-top:1px solid var(--rule)}
.welcome p{position:absolute;left:98px;top:86px;width:848px;font-size:10.9px;line-height:17.4px;text-align:justify}
.welcome p b{font-style:italic}
.btn{position:absolute;left:866px;top:169px;width:77px;height:25px;line-height:25px;text-align:center;background:var(--green);color:#fff;font-family:"Open Sans",sans-serif;font-weight:700;font-size:9.5px}
.lower{position:absolute;left:0;top:855px;width:1041px;height:287px;background:var(--lower-bg)}
.lower h2{position:absolute;color:#2a2a2a}
.pager{position:absolute;display:flex;gap:3px}
.pager span{width:17px;height:17px;border-radius:50%;background:#c9c9c9}
.pager span+span{background:#9a9a9a}
.events-rule{position:absolute;left:84px;top:65px;width:249px;border-top:1px solid var(--rule)}
.divider{position:absolute;left:346px;top:35px;height:215px;border-left:1px dotted #aaa}
.events{position:absolute;left:106px;top:82px;width:211px;list-style:none}
.events li{position:relative;padding:0 0 12px 16px;margin-bottom:10px;font-size:10.8px;line-height:14px;color:var(--text);border-bottom:1px solid #cfd8e6}
.events li:last-child{border:0}
.events li::before{content:"";position:absolute;left:0;top:3px;width:8px;height:8px;border-radius:50%;background:#bcd3ef}
.member-rule{position:absolute;left:362px;top:65px;width:592px;border-top:1px solid var(--rule)}
.posts{position:absolute;left:365px;top:80px;width:590px}
.post{margin-bottom:25px}
.post h3{font-size:11px;font-weight:700;color:#333;margin-left:2px}
.post time{display:block;margin:4px 0 11px 2px;font-size:11px;font-weight:700;font-style:italic;color:var(--date)}
.post p{font-size:11px;line-height:14px}
.footer{position:absolute;left:0;top:1142px;width:1041px;height:58px;background:var(--footer-bg);color:#e6e6e6;font-size:11px}
.footer .copy{position:absolute;left:103px;top:24px}
.footer .links{position:absolute;left:671px;top:24px;display:flex;gap:13px}
</style>
</head>
<body>
<div class="hero" role="img" aria-label="Photo of two dentists examining a young patient in a bright treatment room"></div>
<svg class="header-curve" width="1041" height="125" viewBox="0 0 1041 125">
  <path d="M0 0H1041V26Q700 85 330 112Q120 125 0 60Z" fill="#fff"/>
  <path d="M0 60Q120 125 330 112Q700 85 1015 32Q700 98 330 124Q110 132 0 78Z" fill="#9fd000"/>
</svg>
<div class="brand"><span class="brand-mark"></span><span class="brand-name">ASHFORD<br>DENTAL</span></div>
<div class="contact">
  <svg width="12" height="16" viewBox="0 0 12 16"><path d="M3 1l3 3-2 2q1 4 4 6l2-2 2 3-2 2Q3 14 1 3Z" fill="#222"/></svg>
  <small>Call Us:</small><strong>555-014-2290</strong>
</div>
<div class="social"><span></span><span></span><span></span></div>

<div class="patient-actions">
  <a class="action-appointment" href="#">Request an Appointment</a>
  <a class="action-forms" href="#">Patient Forms</a>
</div>

<nav class="nav">
  <a class="active" href="#" style="left:111px">Home</a>
  <i style="left:219px"></i><a href="#" style="left:239px">Dentists Staff</a>
  <i style="left:364px"></i><a href="#" style="left:393px">Services</a>
  <i style="left:481px"></i><a href="#" style="left:516px">Location</a>
  <i style="left:604px"></i><a href="#" style="left:639px">Specialist</a>
  <i style="left:743px"></i><a href="#" style="left:769px">Contact Us</a>
</nav>

<section class="welcome">
  <h2>Welcome <em>Message</em></h2>
  <hr>
  <p><b>Lorem ipsum dolor sit amet, consectetur adipiscing elit. Phasellus vitae eros et lorem tempus adipiscing. Cras in nulla ipsum. Donec et purus eget</b> risus dapibus lacinia. Etiam elementum, mi vitae iaculis dictum, nulla enim tempus tellus, at pretium ipsum tortor aliquet nunc. Praesent euismod nulla vel arcu pellentesque aliquam. Nulla blandit vulputate nisl in feugiat. Pellentesque vulputate laoreet faucibus. Etiam hendrerit molestie elit, vitae ullamcorper ligula dignissim sit amet. Etiam vulputate magna quis quam adipiscing eu pharetra orci condimentum.</p>
  <a class="btn">View Details »</a>
</section>

<section class="lower">
  <h2 style="left:99px;top:17px">Upcoming <em>Events</em></h2>
  <div class="pager" style="left:300px;top:40px"><span></span><span></span></div>
  <div class="events-rule"></div>
  <ul class="events">
    <li>Mauris justo tellus, convallis nec dignissim nec, varius quis libero.</li>
    <li>Mauris justo tellus, convallis nec dignissim nec, varius quis libero.</li>
    <li>Mauris justo tellus, convallis nec dignissim nec, varius quis libero.</li>
  </ul>
  <div class="divider"></div>
  <h2 style="left:370px;top:20px">Member's <em>Area</em></h2>
  <div class="pager" style="left:896px;top:39px"><span></span><span></span></div>
  <div class="member-rule"></div>
  <div class="posts">
    <article class="post">
      <h3>Morbi adipiscing, augue et tincidunt vulputate, sapien mi facilisis turpis</h3>
      <time>Posted on : 12-02-13</time>
      <p>Aliquam et mauris mauris, et tempus tellus. Suspendisse placerat pretium nisi, nec pellentesque arcu vulputate at. Nulla gravida iaculis urna, eget eleifend odio malesuada non. Nulla facilisi.</p>
    </article>
    <article class="post">
      <h3>Vestibulum egestas tincidunt sapien id vulputate. Nullam id orci turpis, eget varius lacus.</h3>
      <time>Posted on : 12-02-13</time>
      <p>Aliquam et mauris mauris, et tempus tellus. Suspendisse placerat pretium nisi, nec pellentesque arcu vulputate at. Nulla gravida iaculis urna, eget eleifend odio malesuada non. Nulla facilisi.</p>
    </article>
  </div>
</section>

<footer class="footer">
  <span class="copy">Copyright &nbsp;&nbsp;2014 Ashford Dental, All rights reserved</span>
  <span class="links"><span>Legal Notice</span><span>~</span><span>Sitemap</span><span>~</span><span>Contact Us</span></span>
</footer>
</body>
</html>
```